Investment company needing business card

We are wanting a business card which looks sharp and easy on the eye. We are thinking of having a business card with the logo embossed on it, to really make it stand out. We will only have a small amount of information of the business card, person's name, position, email address and phone number

Contact Information for Business Card

Danielle Frost
Executive Assistant
+64 21 473 5162
danielf@harwickpartners.co.nz

Requirements
Must have
• Embossed logo
Should not have
• Not to be busy

```html
<!DOCTYPE html>
<html lang="en">
<head>
<meta charset="utf-8">
<title>Harwick Partners – Business Cards</title>
<link rel="stylesheet" href="https://fonts.googleapis.com/css2?family=Michroma&family=Open+Sans:wght@400&display=swap">
<style>
  :root {
    --green: #2bb673;
    --frame-grey: #5c5c5c;
    --mark-grey: #666666;
    --leather-light: #3b3b3b;
    --leather-dark: #1c1c1c;
    --paper: #ffffff;
    --title-grey: #a9a9a9;
    --contact-light: #dedede;
    --contact-dark: #555555;
    --backdrop-centre: #ececec;
    --backdrop-edge: #b4b4b4;
  }
  * { margin: 0; padding: 0; box-sizing: border-box; }
  html, body { width: 1200px; height: 788px; overflow: hidden; }
  body {
    background: radial-gradient(ellipse at 50% 50%, var(--backdrop-centre) 0%, var(--backdrop-edge) 100%);
    font-family: "Open Sans", Arial, sans-serif;
  }
  .stage {
    position: absolute; left: 0; top: 0;
    width: 1101px; height: 723px;
    transform: scale(1.0899);
    transform-origin: 0 0;
  }
  .card {
    position: absolute;
    width: 506px; height: 291px;
    overflow: hidden;
    box-shadow: 0 2px 6px rgba(0,0,0,0.25);
  }
  .card svg.card-shapes { position: absolute; inset: 0; width: 100%; height: 100%; }
  .card--front-dark { left: 32px; top: 45px; border-radius: 25px 0 0 25px; }
  .card--front-light { left: 557px; top: 45px; border-radius: 30px 0 0 30px; }
  .card--back { left: 320px; top: 367px; border-radius: 0 0 0 25px; }

  .brand { position: absolute; display: flex; align-items: center; gap: 10px; }
  .brand__square { width: 46px; height: 46px; background: var(--mark-grey); }
  .brand__name {
    font-family: "Michroma", Arial, sans-serif;
    font-size: 17px; color: var(--green); letter-spacing: 0.5px;
    white-space: nowrap;
  }
  .card--front-dark .brand, .card--front-light .brand { left: 34px; top: 58px; }

  .contacts {
    position: absolute; left: 34px; top: 175px;
    list-style: none; font-size: 12.5px; line-height: 20px;
  }
  .contacts li { display: flex; align-items: center; gap: 7px; }
  .contacts svg { width: 11px; height: 11px; flex: none; }
  .card--front-dark .contacts { color: var(--contact-light); }
  .card--front-light .contacts { color: var(--contact-dark); }

  .person { position: absolute; right: 58px; top: 176px; text-align: right; }
  .person__name {
    font-family: "Michroma", Arial, sans-serif;
    font-size: 14px; color: var(--green); line-height: 20px;
  }
  .person__title {
    font-family: "Michroma", Arial, sans-serif;
    font-size: 11px; color: var(--title-grey); line-height: 22px;
    letter-spacing: 0.3px;
  }
  .card--front-light .person__title { color: #8a8a8a; }

  .back-square {
    position: absolute; left: 28px; top: 50px;
    width: 200px; height: 195px;
    background: var(--mark-grey);
    box-shadow: 2px 3px 4px rgba(0,0,0,0.5);
  }
  .card--back .brand { left: 280px; top: 119px; }
  .card--back .brand__name { font-size: 12.5px; letter-spacing: 0.4px; }
  .card--back .web {
    position: absolute; left: 285px; top: 168px;
    display: flex; align-items: center; gap: 6px;
    font-size: 12.5px; color: var(--contact-light);
  }
  .card--back .web svg { width: 11px; height: 11px; }
</style>
</head>
<body>
<div class="stage">

  <!-- Front, dark edition -->
  <section class="card card--front-dark">
    <svg class="card-shapes" viewBox="0 0 506 291" preserveAspectRatio="none">
      <defs>
        <radialGradient id="leather-a" cx="40%" cy="40%" r="80%">
          <stop offset="0" stop-color="var(--leather-light)"/>
          <stop offset="1" stop-color="var(--leather-dark)"/>
        </radialGradient>
      </defs>
      <rect width="506" height="291" fill="url(#leather-a)" role="img" aria-label="Dark embossed leather texture"/>
      <rect width="506" height="27" fill="var(--green)"/>
      <path d="M0 27H26V240Q26 265 51 265H483V213H458V205H506V291H0Z" fill="var(--frame-grey)"/>
    </svg>
    <div class="brand"><span class="brand__square"></span><span class="brand__name">HARWICK PARTNERS</span></div>
    <ul class="contacts">
      <li><svg viewBox="0 0 12 12"><circle cx="6" cy="6" r="5.5" fill="var(--green)"/><path d="M4 3.2l1.2 1.4-.6.7c.4.9 1 1.5 1.9 1.9l.7-.6 1.4 1.2-.8 1C5.6 8.6 3.4 6.4 3.2 4z" fill="#1c1c1c"/></svg>+64 21 473 5162</li>
      <li><svg viewBox="0 0 12 12"><rect x="1" y="3" width="10" height="7" fill="var(--green)"/><path d="M1 3l5 4 5-4" stroke="#1c1c1c" fill="none"/></svg>danielf@harwickpartners.co.nz</li>
      <li><svg viewBox="0 0 12 12"><circle cx="6" cy="6" r="5.5" fill="var(--green)"/><path d="M.5 6h11M6 .5v11M2 3h8M2 9h8" stroke="#1c1c1c" stroke-width=".8"/></svg>www.harwickpartners.com</li>
    </ul>
    <div class="person">
      <p class="person__name">DANIELLE FROST</p>
      <p class="person__title">EXECUTIVE ASSISTANT</p>
    </div>
  </section>

  <!-- Front, light edition -->
  <section class="card card--front-light">
    <svg class="card-shapes" viewBox="0 0 506 291" preserveAspectRatio="none">
      <rect width="506" height="291" fill="var(--paper)"/>
      <rect width="506" height="27" fill="var(--green)"/>
      <path d="M0 27H26V236Q26 265 55 265H483V213H458V205H506V291H0Z" fill="var(--frame-grey)"/>
    </svg>
    <div class="brand"><span class="brand__square"></span><span class="brand__name">HARWICK PARTNERS</span></div>
    <ul class="contacts">
      <li><svg viewBox="0 0 12 12"><circle cx="6" cy="6" r="5.5" fill="var(--green)"/><path d="M4 3.2l1.2 1.4-.6.7c.4.9 1 1.5 1.9 1.9l.7-.6 1.4 1.2-.8 1C5.6 8.6 3.4 6.4 3.2 4z" fill="#fff"/></svg>+64 21 473 5162</li>
      <li><svg viewBox="0 0 12 12"><rect x="1" y="3" width="10" height="7" fill="var(--green)"/><path d="M1 3l5 4 5-4" stroke="#fff" fill="none"/></svg>danielf@harwickpartners.co.nz</li>
      <li><svg viewBox="0 0 12 12"><circle cx="6" cy="6" r="5.5" fill="var(--green)"/><path d="M.5 6h11M6 .5v11M2 3h8M2 9h8" stroke="#fff" stroke-width=".8"/></svg>www.harwickpartners.com</li>
    </ul>
    <div class="person">
      <p class="person__name">DANIELLE FROST</p>
      <p class="person__title">EXECUTIVE ASSISTANT</p>
    </div>
  </section>

  <!-- Back -->
  <section class="card card--back">
    <svg class="card-shapes" viewBox="0 0 506 291" preserveAspectRatio="none">
      <defs>
        <radialGradient id="leather-b" cx="50%" cy="40%" r="80%">
          <stop offset="0" stop-color="var(--leather-light)"/>
          <stop offset="1" stop-color="var(--leather-dark)"/>
        </radialGradient>
      </defs>
      <rect width="506" height="291" fill="url(#leather-b)" role="img" aria-label="Dark embossed leather texture"/>
    </svg>
    <div class="back-square"></div>
    <div class="brand"><span class="brand__name">HARWICK PARTNERS</span></div>
    <p class="web"><svg viewBox="0 0 12 12"><circle cx="6" cy="6" r="5.5" fill="var(--green)"/><path d="M.5 6h11M6 .5v11M2 3h8M2 9h8" stroke="#1c1c1c" stroke-width=".8"/></svg>www.harwickpartners.com/</p>
  </section>

</div>
</body>
</html>
```